Brightfen Business Card Redesign & Logo Update

We need to update our business cards to something more modern and fresh. Brightfen can provide the current color schemes and old design examples, but welcome creativity in helping us with this redesign. PLEASE NOTE that we no longer utilize the "tree" and/or "leaf" imagery in our branding. If able would apprecaite an update on the quality of our "words only" logo in Ai. / PNG formats too.

Target Market(s)

Investors, landowners, corporate partners, contractors

Industry/Entity Type

Environmental Restoration & Conservation

Contact Information for Business Card

Logo, persons name, title, mailing address, phone and email, website url

Font styles to use
Other font styles liked:
• Merriweather

Requirements
Nice to have
• Logo, persons name, title, mailing address, phone and email, website url, but open to ideams
Should not have
• No all back backgrounds

```html
<!DOCTYPE html>
<html lang="en">
<head>
<meta charset="utf-8">
<title>Brightfen Business Cards</title>
<link rel="stylesheet" href="https://fonts.googleapis.com/css2?family=Open+Sans:wght@400;700&display=swap">
<style>
  :root {
    --stage: #2c2c2f;
    --card: #222226;
    --orange: #ef7f22;
    --green: #127c3e;
    --white: #ffffff;
  }
  * { margin: 0; padding: 0; box-sizing: border-box; }
  html, body { width: 1200px; height: 780px; overflow: hidden; }
  body {
    background: var(--stage);
    position: relative;
    font-family: "Open Sans", Arial, sans-serif;
  }
  .card {
    position: absolute;
    width: 560px;
    height: 320px;
    background: var(--card);
    overflow: hidden;
    box-shadow: 0 10px 24px rgba(0,0,0,.45);
  }
  .card--front { left: 60px; top: 60px; }
  .card--back { left: 580px; top: 400px; }

  .wordmark {
    position: absolute;
    font-family: "Open Sans", Arial, sans-serif;
    font-weight: 700;
    color: var(--orange);
    text-transform: uppercase;
    line-height: 1;
  }
  .card--front .wordmark {
    left: 0; right: 0; top: 118px;
    text-align: center;
    font-size: 72px;
    letter-spacing: 1px;
  }
  .card--back .wordmark {
    left: 34px; top: 112px;
    font-size: 36px;
  }

  .divider {
    position: absolute;
    left: 282px; top: 70px;
    width: 1.5px; height: 150px;
    background: var(--white);
  }
  .contact {
    position: absolute;
    left: 312px; top: 70px;
    color: var(--white);
  }
  .person-name {
    font-size: 23px;
    font-weight: 700;
    color: var(--green);
    line-height: 1.1;
  }
  .person-name .surname { color: var(--orange); }
  .person-title {
    font-size: 14px;
    margin-top: 2px;
    margin-left: 18px;
  }
  .contact-list {
    list-style: none;
    margin-top: 16px;
    margin-left: 18px;
    font-size: 13.5px;
  }
  .contact-list li {
    display: flex;
    align-items: center;
    gap: 10px;
    height: 22px;
  }
  .contact-list svg { width: 14px; height: 14px; flex: none; }
  .swoosh {
    position: absolute;
    left: 0; bottom: 0;
    width: 560px; height: 320px;
  }
</style>
</head>
<body>
  <section class="card card--front" aria-label="Card front">
    <div class="wordmark">Brightfen</div>
  </section>

  <section class="card card--back" aria-label="Card back">
    <svg class="swoosh" viewBox="0 0 560 320" aria-hidden="true">
      <path d="M90 320 C 260 290, 430 230, 560 150 L560 320 Z" fill="var(--green)"/>
      <path d="M270 262 C 380 240, 480 200, 560 140 L560 132 C 480 190, 380 232, 270 262 Z" fill="var(--orange)"/>
    </svg>

    <div class="wordmark">Brightfen</div>
    <div class="divider"></div>

    <div class="contact">
      <h1 class="person-name">Lenka <span class="surname">Horakova</span></h1>
      <p class="person-title">Managing Director</p>
      <ul class="contact-list">
        <li>
          <svg viewBox="0 0 24 24" aria-hidden="true"><path fill="var(--green)" d="M6.6 10.8a15.1 15.1 0 0 0 6.6 6.6l2.2-2.2a1 1 0 0 1 1-.25 11.4 11.4 0 0 0 3.6.6 1 1 0 0 1 1 1V20a1 1 0 0 1-1 1A17 17 0 0 1 3 4a1 1 0 0 1 1-1h3.5a1 1 0 0 1 1 1c0 1.25.2 2.45.6 3.6a1 1 0 0 1-.25 1z"/></svg>
          (555) 014-2287
        </li>
        <li>
          <svg viewBox="0 0 24 24" aria-hidden="true"><rect x="2" y="5" width="20" height="14" rx="1.5" fill="var(--green)"/><path d="M3 6l9 7 9-7" fill="none" stroke="var(--card)" stroke-width="1.8"/></svg>
          hello@brightfen.com
        </li>
        <li>
          <svg viewBox="0 0 24 24" aria-hidden="true"><circle cx="12" cy="12" r="10" fill="var(--green)"/><path d="M2 12h20M12 2c3 3 3 17 0 20M12 2c-3 3-3 17 0 20" fill="none" stroke="var(--card)" stroke-width="1.4"/></svg>
          www.brightfen.com
        </li>
      </ul>
    </div>
  </section>
</body>
</html>
```